Brightway Haus Inc. Business Card Design

Brightway Haus Inc. is in search of a great clean design for our business cards!

Looking to incorporate our full logo and watermark on side one (however, I am open to having the text and watermark separated within the design.)

On side two, I am looking to have contact information (Name, Position, Phone #, Email, Website (www.thebrightwayhaus.ca). Can have the logo and/or watermark as part of the design if applicable.

Please add tagline "Where Shine Counts" on either side 1 or 2. This tagline can be in a sans serif, serif or cursive font as long as it compliments overall design. Capitalization can be title or sentence case depending on how it fits within the design.

Get creative!! Looking for a clean, crisp, premium design! Looking for a glossy card finish with spot UV features when printed. Cards will also be printed with rounded corners. Standard dimensions (3.5 x 2).

Target Market(s)

B2B - primary clients are business owners or property management corporations. (residential jobs are few and far between)

Industry/Entity Type

Business

Contact Information for Business Card

- clean, crisp design
- double sided
- spot UV accents and glossy finish upon printing
- standard business card size (3.5 x 2) with rounded corners
- please see project description for requirements per side

Font styles to use
Sans Serif

Requirements
Must have
• - adequate bleeds with print ready files
• - cohesive design elements between side 1 & 2
• - spot UV elements (can be on both sides or just one, use your discretion)
• - colour pallet should match the logo file provided
• - incorporate tagline "where shine counts" (this tagline can be in a serif or sans serif font as long as it is complimentary to the overall design.
Nice to have
• - Premium elements with a clean design
Should not have
• - Please omit cartoon or whimsical like designs, think premium.
• - Colours should not stray from the pallet of the provided logo.

```html
<!DOCTYPE html>
<html lang="en">
<head>
<meta charset="utf-8">
<title>Brightway Haus Inc. Business Cards</title>
<link href="https://fonts.googleapis.com/css2?family=PT+Sans:wght@400;700&display=swap" rel="stylesheet">
<style>
  :root {
    --navy: #1b2150;
    --teal: #12b8bb;
    --white: #ffffff;
    --silver: #c9ccd6;
    --backdrop: #e6e7ea;
  }
  html, body {
    margin: 0;
    padding: 0;
    width: 1200px;
    height: 960px;
    overflow: hidden;
    background: var(--backdrop);
    font-family: "PT Sans", Arial, sans-serif;
  }
  .canvas {
    position: relative;
    width: 1200px;
    height: 960px;
  }
  .card {
    position: absolute;
    width: 600px;
    height: 343px;
    border-radius: 22px;
    overflow: hidden;
    box-shadow: 0 3px 8px rgba(0,0,0,0.25);
  }
  .card--front { left: 314px; top: 113px; background: var(--white); }
  .card--back { left: 311px; top: 472px; background: var(--navy); }

  .front-wave { position: absolute; inset: 0; width: 600px; height: 343px; }

  .brand-name {
    position: absolute;
    left: 31px;
    top: 46px;
    margin: 0;
    font-size: 27px;
    font-weight: 700;
    letter-spacing: -0.3px;
    color: var(--navy);
    line-height: 1;
  }
  .holder { position: absolute; left: 31px; top: 104px; }
  .holder__name {
    margin: 0;
    font-size: 17px;
    font-weight: 700;
    color: var(--teal);
    line-height: 1.2;
  }
  .holder__role {
    margin: 2px 0 0;
    font-size: 16px;
    color: var(--navy);
    line-height: 1.2;
  }

  .contact {
    position: absolute;
    right: 31px;
    top: 182px;
    color: var(--white);
    font-size: 14.5px;
    text-align: right;
    line-height: 19.5px;
  }
  .contact__address { margin: 0 0 7px; padding-right: 0; }
  .contact__list { list-style: none; margin: 0; padding: 0; }
  .contact__item { display: flex; justify-content: flex-end; align-items: center; gap: 8px; }
  .contact__icon { width: 12px; height: 12px; fill: var(--white); flex: none; }

  .back-brand {
    position: absolute;
    left: 0;
    right: 0;
    top: 143px;
    margin: 0;
    text-align: center;
    font-size: 42px;
    font-weight: 700;
    letter-spacing: -0.5px;
    color: var(--silver);
    line-height: 1;
  }
  .tagline {
    position: absolute;
    left: 0;
    right: 0;
    top: 276px;
    display: flex;
    justify-content: center;
    align-items: center;
    gap: 4px;
    color: var(--white);
    font-size: 17px;
    font-weight: 700;
  }
  .tagline__rule {
    width: 115px;
    height: 1px;
  }
  .tagline__rule--left { background: linear-gradient(to right, rgba(255,255,255,0), rgba(255,255,255,0.9)); }
  .tagline__rule--right { background: linear-gradient(to left, rgba(255,255,255,0), rgba(255,255,255,0.9)); }
</style>
</head>
<body>
<main class="canvas">

  <section class="card card--front" aria-label="Business card front">
    <svg class="front-wave" viewBox="0 0 600 343" aria-hidden="true">
      <path d="M0,302 C150,228 330,124 470,124 C525,124 565,145 600,192 L600,343 L0,343 Z" fill="var(--navy)"/>
      <path d="M0,334 C150,252 330,134 478,131 C538,130 582,162 600,200 L600,343 L0,343 Z" fill="var(--teal)" stroke="var(--white)" stroke-width="2"/>
    </svg>

    <h1 class="brand-name">BRIGHTWAY HAUS INC.</h1>

    <div class="holder">
      <p class="holder__name">DANIEL HARTLEY</p>
      <p class="holder__role">CEO/FOUNDER</p>
    </div>

    <address class="contact" style="font-style:normal">
      <p class="contact__address">2140 Larkspur Road<br>Kelowna, BC V1Y 4R2</p>
      <ul class="contact__list">
        <li class="contact__item">250 555 0142
          <svg class="contact__icon" viewBox="0 0 12 12"><path d="M1,4 C1,2 3,1 6,1 C9,1 11,2 11,4 L8.5,4.5 L8,3 L4,3 L3.5,4.5 Z M3,6 L9,6 L10.5,11 L1.5,11 Z"/></svg>
        </li>
        <li class="contact__item">250 555 0187
          <svg class="contact__icon" viewBox="0 0 12 12"><path d="M3,0.5 H9 V11.5 H3 Z M4.2,1.8 V9.5 H7.8 V1.8 Z"/></svg>
        </li>
        <li class="contact__item">250 555 0199
          <svg class="contact__icon" viewBox="0 0 12 12"><path d="M3,1 H9 V4 H3 Z M1,4.8 H11 V9 H9 V11 H3 V9 H1 Z M4,8 V10 H8 V8 Z"/></svg>
        </li>
        <li class="contact__item">hello@thebrightwayhaus.ca
          <svg class="contact__icon" viewBox="0 0 12 12"><path d="M1,2.5 H11 V3.2 L6,6.5 L1,3.2 Z M1,4.4 L6,7.7 L11,4.4 V9.5 H1 Z"/></svg>
        </li>
        <li class="contact__item">www.thebrightwayhaus.ca
          <svg class="contact__icon" viewBox="0 0 12 12"><circle cx="6" cy="6" r="5.5"/><path d="M3,4 C4,3 5,4 4.5,5.5 C4,7 5.5,7.5 5,9.5 M8,2.5 C7,4 8.5,5 9.5,5" stroke="var(--teal)" stroke-width="1" fill="none"/></svg>
        </li>
      </ul>
    </address>
  </section>

  <section class="card card--back" aria-label="Business card back">
    <h2 class="back-brand">BRIGHTWAY HAUS INC.</h2>
    <p class="tagline" style="margin:0">
      <span class="tagline__rule tagline__rule--left"></span>
      <span class="tagline__text">Where Shine Counts</span>
      <span class="tagline__rule tagline__rule--right"></span>
    </p>
  </section>

</main>
</body>
</html>
```